We (R. T. Galvin & Partners, Inc.) are an executive Search firm based in Los Angeles that is exclusively focused in the Med Tech and Health Tech arenas.   I need a logo to communicate that we are a high end search firm, but also that we are focused in the medicine and science arenas called health tech and med tech.  Many of our clients have robotics and artificial intelligence type products, so it is very technology forward.  I tend to gravitate towards clean, sharp aesthetic as opposed to something that is really over the top.
Attached are files with my logo in two different layouts.  In addition to the letterhead and envelope, I also will need an electronic letterhead in Microsoft Word.  I tend to
I look forward to seeing the designs and just let me know if you have any questions.
Dale

```html
<!DOCTYPE html>
<html lang="en">
<head>
<meta charset="utf-8">
<title>R. T. Galvin &amp; Partners, Inc. — Stationery</title>
<link rel="stylesheet" href="https://fonts.googleapis.com/css2?family=Montserrat:wght@300;400;500;600&family=Arimo:wght@400&display=swap">
<style>
  :root{
    --board:#a9a9a9;
    --brand-blue:#52a2da;
    --ink:#111111;
    --text-grey:#8a8a8a;
    --paper-white:#ffffff;
    --paper-grey:#e4e4e4;
    --shadow:0 2px 4px rgba(0,0,0,.35);
  }
  *{box-sizing:border-box;margin:0;padding:0}
  html,body{width:1200px;height:1190px;overflow:hidden;background:var(--board)}
  body{position:relative;font-family:"Montserrat",sans-serif;color:var(--ink)}

  .sheet{position:absolute;background:linear-gradient(100deg,var(--paper-grey) 0%,#f6f6f6 45%,var(--paper-white) 100%);box-shadow:var(--shadow);overflow:hidden}
  .header-band{position:absolute;left:0;top:0;width:100%;background:var(--brand-blue);border-bottom:3px solid var(--ink)}

  .brand{display:flex;align-items:center;gap:7px;white-space:nowrap}
  .brand-dot{border-radius:50%;background:var(--brand-blue);flex:none}
  .brand-name{font-weight:600;letter-spacing:.01em}

  /* Letterhead */
  .letterhead{left:40px;top:50px;width:556px;height:786px}
  .letterhead .header-band{height:22px}
  .letterhead .brand{position:absolute;left:44px;top:86px}
  .letterhead .brand-dot{width:12px;height:12px}
  .letterhead .brand-name{font-size:15px}
  .letter-to{position:absolute;left:57px;top:180px;font-size:10px;letter-spacing:.15em}
  .letter-date{position:absolute;right:56px;top:180px;font-size:8px;font-weight:300;color:#555}
  .recipient{position:absolute;left:57px;top:197px;font-size:7.6px;font-weight:300;color:var(--text-grey);line-height:12px}
  .recipient .recipient-name{color:var(--brand-blue);font-size:9.5px;font-weight:500;margin-bottom:2px}
  .letter-body{position:absolute;left:57px;top:283px;width:444px;font-size:7.9px;font-weight:300;line-height:10px;color:var(--text-grey);text-align:justify}
  .letter-body p{margin-bottom:10px}
  .signature{position:absolute;left:56px;top:556px;width:100px;height:22px;background:linear-gradient(90deg,#dcdcdc,#eeeeee)}
  .signer{position:absolute;left:56px;top:586px;font-size:8.6px;font-weight:500;letter-spacing:.03em}
  .signer-role{position:absolute;left:55px;top:598px;font-size:7.4px;font-weight:300;color:var(--text-grey)}
  .letter-footer{position:absolute;left:124px;top:732px;width:307px;font-family:"Arimo",sans-serif;font-size:9.6px;text-align:center}
  .letter-footer .address{padding-bottom:5px;border-bottom:1px solid #333}
  .contact-row{display:flex;justify-content:center;align-items:center;gap:5px;margin-top:6px;white-space:nowrap}
  .contact-row svg{width:8px;height:8px;flex:none}
  .contact-row span{margin-right:4px}

  /* Folder cover */
  .folder-cover{position:absolute;left:622px;top:50px;width:538px;height:380px;box-shadow:var(--shadow)}
  .folder-back{position:absolute;left:0;top:0;width:268px;height:100%;background:var(--brand-blue)}
  .folder-front{left:268px;top:0;width:270px;height:100%;box-shadow:none}
  .folder-front .header-band{height:12px;border-bottom-width:2px}
  .folder-front .brand{position:absolute;left:60px;top:180px}
  .folder-front .brand-dot{width:10px;height:10px}
  .folder-front .brand-name{font-size:12.5px}
  .cover-contact{position:absolute;left:96px;top:348px;display:flex;gap:4px;font-family:"Arimo",sans-serif;font-size:3.8px;line-height:5px}
  .cover-contact .cover-address{text-align:right;padding-right:4px;border-right:.6px solid #333}

  /* Folder open */
  .folder-open{position:absolute;left:623px;top:458px;width:535px;height:378px;box-shadow:var(--shadow);background:#c9c9c9;overflow:hidden}
  .folder-panel-left{position:absolute;left:0;top:0;width:267px;height:100%;background:linear-gradient(90deg,#fff,#e3e3e3)}
  .folder-panel-right{position:absolute;left:269px;top:0;width:266px;height:100%;background:linear-gradient(90deg,#e6e6e6,#fff)}
  .mini-letter{left:281px;top:18px;width:242px;height:230px;box-shadow:none;background:linear-gradient(100deg,#ececec,#fff)}
  .mini-letter .header-band{height:10px;border-bottom-width:2px}
  .mini-letter .brand{position:absolute;left:16px;top:36px;gap:3px}
  .mini-letter .brand-dot{width:5px;height:5px}
  .mini-letter .brand-name{font-size:6px}
  .mini-to{position:absolute;left:25px;top:93px;font-size:3.6px;letter-spacing:.15em}
  .mini-date{position:absolute;right:24px;top:93px;font-size:2.8px;color:#666}
  .mini-recipient{position:absolute;left:25px;top:100px;font-size:2.6px;line-height:4px;color:var(--text-grey)}
  .mini-recipient .recipient-name{color:var(--brand-blue);font-size:3.2px}
  .mini-body{position:absolute;left:25px;top:130px;width:192px;font-size:2.9px;line-height:3.6px;color:var(--text-grey);text-align:justify}
  .mini-body p{margin-bottom:3.4px}
  .pockets{position:absolute;left:0;top:0;width:535px;height:378px}

  /* Envelope front */
  .envelope{left:40px;top:864px;width:548px;height:238px}
  .envelope .header-band{height:20px}
  .envelope .brand{position:absolute;left:40px;top:49px}
  .envelope .brand-dot{width:11px;height:11px}
  .envelope .brand-name{font-size:13.5px}
  .envelope-address{position:absolute;left:72px;top:70px;font-family:"Arimo",sans-serif;font-size:8px;line-height:10px}

  /* Envelope back */
  .envelope-back{left:625px;top:869px;width:527px;height:229px;background:linear-gradient(100deg,#e9e9e9,#fff)}
  .envelope-flap{position:absolute;left:0;top:0;width:527px;height:64px}
  .envelope-back .brand{position:absolute;left:200px;top:22px}
  .envelope-back .brand-dot{width:10px;height:10px}
  .envelope-back .brand-name{font-size:12px;color:var(--paper-white)}
</style>
</head>
<body>

<svg width="0" height="0" style="position:absolute">
  <defs>
    <symbol id="icon-phone" viewBox="0 0 10 10"><path d="M2,1 L4,1 L4.6,3.2 L3.4,4 C4,5.4 4.8,6.2 6,6.8 L6.8,5.6 L9,6.2 L9,8.2 C9,8.7 8.6,9 8,9 C4.4,8.6 1.4,5.6 1,2 C1,1.4 1.4,1 2,1 Z" fill="#52a2da"/></symbol>
    <symbol id="icon-mail" viewBox="0 0 10 10"><rect x="1" y="2.5" width="8" height="5.5" fill="#52a2da"/><path d="M1,2.5 L5,5.6 L9,2.5" stroke="#fff" stroke-width=".8" fill="none"/></symbol>
    <symbol id="icon-web" viewBox="0 0 10 10"><circle cx="5" cy="5" r="4" fill="#52a2da"/><path d="M1,5 H9 M5,1 C3,3 3,7 5,9 M5,1 C7,3 7,7 5,9" stroke="#fff" stroke-width=".6" fill="none"/></symbol>
  </defs>
</svg>

<!-- Letterhead -->
<section class="sheet letterhead">
  <div class="header-band"></div>
  <div class="brand"><span class="brand-dot"></span><span class="brand-name">R. T. Galvin &amp; Partners, Inc.</span></div>
  <div class="letter-to">TO</div>
  <div class="letter-date">Friday, 01/01/2018</div>
  <div class="recipient">
    <div class="recipient-name">Alan Whitford</div>
    Human Resources<br>Brightline Labs Inc.<br>2240 Harbor Lane, Westfield<br>CA 90012 USA
  </div>
  <div class="letter-body">
    <p>Lorem ipsum dolor sit amet, consectetuer adipiscing elit, sed diam nonmmy nibh euismod tincidunt ut laoreet dolore magna aliquam erat volutpat. Ut wisi enim ad minim veniam, quis nostrud exerci tationmcorper suscipit lobortis nisl ut aliquip ex ea commodo consequat. Duis autem vel eum iriure dolor in hendrerit in vulputate velit esse molestie consequat, vel illum dolore eu feugiat nulla facilisis at vero eros et accumsan et iusto odio dignissim qui blandit praesent luptatum zzril delenit augue duis dolore te feugait nulla facilisi.</p>
    <p>Nam liber tempor cum soluta nobis eleifend option congue nihil imprdiet doming id quod mazim placerat facer possim assum. Typi non habent claritatem insitam;</p>
    <p>Est usus legentis in iis qui facit eorum claritatem.</p>
    <p>Investigationes demonstraverunt lectores legere me lius quod ii legunt saepius. Claritas est etiam processus dynamicus, qui sequitur mutationem consuetudium lectorum. Mirum est notare quam littera gothica, quam nunc putamus parum claram, anteposuerit litterarum formas humanitatis per seacula quarta decima et quinta decima. Eodem modo typi, qui nunc nobis videntur parum clari, fiant sollemnes in futurum.</p>
    <p>consectetuer adipiscing elit, sed diam nonummy nibh euismod tincidunt ut laoreet dolore magna aliquam erat volutpat. Ut wisi enim ad minim veniam, quis nostrud exerci tation ullamcorper suscipit lobortis nisl ut aliquip ex ea commodo consequat. Duis autem vel eum iriure dolor in hendrerit in vulputate velit esse molestie consequat, vel illum dolore eu feugiat nulla facilisis at vero eros et accumsan et iusto odio dignissim qui blandit praesent luptatum zzril delenit augue duis dolore te feugait nulla facilisi.</p>
    <p>Nam liber tempor cum soluta nobis eleifend option congue nihil imperdiet .</p>
  </div>
  <div class="signature" role="img" aria-label="Handwritten signature of Peter Hale"></div>
  <div class="signer">Peter Hale</div>
  <div class="signer-role">Managing Director</div>
  <footer class="letter-footer">
    <div class="address">1200 Wilshire Blvd, Los Angeles, CA 90017</div>
    <div class="contact-row">
      <svg><use href="#icon-phone"/></svg><span>310-555-0142</span>
      <svg><use href="#icon-mail"/></svg><span>info@galvinpartners.com</span>
      <svg><use href="#icon-web"/></svg><span>www.galvinpartners.com</span>
    </div>
  </footer>
</section>

<!-- Presentation folder, closed -->
<section class="folder-cover">
  <div class="folder-back"></div>
  <div class="sheet folder-front">
    <div class="header-band"></div>
    <div class="brand"><span class="brand-dot"></span><span class="brand-name">R. T. Galvin &amp; Partners, Inc.</span></div>
    <div class="cover-contact">
      <div class="cover-address">1200 Wilshire Blvd,<br>Los Angeles, CA 90017</div>
      <div>310-555-0142<br>info@galvinpartners.com<br>www.galvinpartners.com</div>
    </div>
  </div>
</section>

<!-- Presentation folder, open -->
<section class="folder-open">
  <div class="folder-panel-left"></div>
  <div class="folder-panel-right"></div>
  <div class="sheet mini-letter">
    <div class="header-band"></div>
    <div class="brand"><span class="brand-dot"></span><span class="brand-name">R. T. Galvin &amp; Partners, Inc.</span></div>
    <div class="mini-to">TO</div>
    <div class="mini-date">Friday, 01/01/2018</div>
    <div class="mini-recipient">
      <div class="recipient-name">Alan Whitford</div>
      Human Resources<br>Brightline Labs Inc.<br>2240 Harbor Lane, Westfield<br>CA 90012 USA
    </div>
    <div class="mini-body">
      <p>We place senior leaders in medical technology and health technology firms across the country, from early robotics teams to growing diagnostic groups that need steady direction.</p>
      <p>Each search is run by a partner who knows the field and the people in it.</p>
      <p>Thank you for your time and your trust.</p>
      <p>Our process begins with a close look at your goals, your team and the role, then moves to a short list of proven candidates within a few weeks.</p>
      <p>We stay involved after the hire to make sure the fit is right for both sides over the first year.</p>
      <p>We look forward to speaking with you soon.</p>
    </div>
  </div>
  <svg class="pockets" viewBox="0 0 535 378">
    <path d="M0,244 H240 Q251,244 249,256 L267,378 H0 Z" fill="#52a2da"/>
    <path d="M535,244 H298 Q288,244 286,256 L268,378 H535 Z" fill="#52a2da"/>
  </svg>
</section>

<!-- Envelope front -->
<section class="sheet envelope">
  <div class="header-band"></div>
  <div class="brand"><span class="brand-dot"></span><span class="brand-name">R. T. Galvin &amp; Partners, Inc.</span></div>
  <div class="envelope-address">1200 Wilshire Blvd,<br>Los Angeles, CA 90017</div>
</section>

<!-- Envelope back -->
<section class="sheet envelope-back">
  <svg class="envelope-flap" viewBox="0 0 527 64">
    <path d="M0,0 H527 L513,44 Q507,63 486,63 H42 Q20,63 14,44 Z" fill="#111"/>
  </svg>
  <div class="brand"><span class="brand-dot"></span><span class="brand-name">R. T. Galvin &amp; Partners, Inc.</span></div>
</section>

</body>
</html>
```